Creation of an elegant and modern turnkey Shopify website

Hello,

We are a new company specializing in the sale of above-ground pools. We want to create a turnkey website, ideally using Shopify. For now, we need a "showcase" site, not an e-commerce platform, with four tabs:

Home Page (an overall presentation of the company)
Our Products (an overview of all the above-ground pools we sell)
Our Projects (a page inspired by Instagram to showcase photos of our future projects)
Contact (a page with all our contact information and a contact form)

We are looking to create a highly visual, elegant, and modern website with vibrant splashes of color. We will provide the text, photos (along with instructions on where to place them on each page), and all other necessary information as attachments.

Thank you in advance for your proposals!

The Brisa Lagoon Team

Target Market(s)

Targeted at Swiss customers (a translator will need to be installed for different languages)

Industry/Entity Type

Sale of customised above-ground pools

Coding

Coded - Design and coding required

Font styles to use
Sans Serif

Colors
0094D4
00A9DD
6FCCEA
C7EBF8
E9F6FB
00AB8E
00BBA5
67D7C9
C6EFE9
E9F9F6

Requirements
Must have
• A stunning, elegant and modern look
Nice to have
• Inspiration from the colors of our logo throughout the site, but in an elegant way
Should not have
• An overly classic look for swimming pool sites

```html
<!DOCTYPE html>
<html lang="en">
<head>
<meta charset="utf-8">
<title>Brisa Lagoon – Above-Ground Pools</title>
<link rel="stylesheet" href="https://fonts.googleapis.com/css2?family=Poppins:wght@300;400;500;600&family=Ubuntu:wght@400;500&display=swap">
<style>
:root{
  --blue:#0094d4;
  --blue-light:#00a9dd;
  --sky:#6fccea;
  --ice:#c7ebf8;
  --mist:#e9f6fb;
  --green:#00ab8e;
  --teal:#00bba5;
  --mint:#67d7c9;
  --foam:#c6efe9;
  --navy:#0a3a5c;
  --sea:#0b7fa8;
  --text:#555b63;
  --white:#fff;
}
*{box-sizing:border-box;margin:0;padding:0}
html,body{width:1200px;height:2734px;overflow:hidden}
body{position:relative;background:#f6fbfd;font-family:"Poppins",sans-serif;color:var(--text)}
.abs{position:absolute}
.page{position:absolute;left:180px;top:0;width:840px;height:2330px;background:var(--white)}
.soft-band{position:absolute;left:180px;top:850px;width:840px;height:1020px;background:#f2f8fb}
.soft-band svg{position:absolute;left:0;top:0}

/* header */
.logo{left:188px;top:16px;font-weight:300;font-size:22px;line-height:24px;color:var(--blue);letter-spacing:1px}
.nav{left:449px;top:33px;display:flex;gap:26px;font-size:12px;font-weight:500;color:#444}
.nav .active{color:var(--blue)}
.call{left:838px;top:24px;display:flex;align-items:center;gap:7px}
.call-icon{width:32px;height:32px;border:1.5px solid var(--blue);border-radius:50%;display:flex;align-items:center;justify-content:center}
.call small{display:block;font-size:9px;color:#555}
.call strong{display:block;font-size:12px;color:var(--blue);font-weight:600;letter-spacing:.2px;white-space:nowrap}

/* hero */
.hero{left:188px;top:78px;width:825px;height:478px;background:linear-gradient(180deg,#2f4a2a 0%,#3d5a34 35%,#6a7d6d 55%,#8a6a4a 75%,#7a5a3d 100%)}
.hero-title{left:188px;top:236px;width:825px;text-align:center;color:#fff;font-weight:600;font-size:29px;line-height:35px}
.hero-sub{left:188px;top:318px;width:825px;text-align:center;color:#fff;font-size:15px}
.btn-hero{left:502px;top:367px;width:196px;height:44px;border-radius:22px;background:var(--teal);color:#fff;font-size:12px;font-weight:500;display:flex;align-items:center;justify-content:center}

.section-title{left:188px;width:825px;text-align:center;font-family:"Ubuntu",sans-serif;font-weight:500;font-size:24px;color:var(--blue)}

/* features */
.features{left:188px;top:661px;width:825px;display:flex;gap:11px}
.feature{width:155px;height:189px;background:#fff;box-shadow:0 0 6px rgba(0,0,0,.07);text-align:center;padding:14px 8px 0}
.feature h3{font-family:"Ubuntu",sans-serif;font-weight:400;font-size:16px;line-height:18px;color:#555}
.feature p{font-size:8.5px;line-height:15px;color:#666;margin-top:12px}
.feature .icon{width:36px;height:36px;margin:10px auto 0;display:block}
.feature.highlight{background:var(--green)}
.feature.highlight h3,.feature.highlight p{color:#fff}

/* gallery */
.photo{position:absolute}
.photo-a{background:linear-gradient(160deg,#2e4a22,#5a7a3a 45%,#4aa6cf 70%,#3a8fbf)}
.photo-b{background:linear-gradient(180deg,#6c8a4a,#2aa1d8 40%,#48b8e6)}
.photo-c{background:linear-gradient(135deg,#e2a24a,#f0c080 30%,#58b7d9 65%,#2a8cc0)}

/* services */
.services{left:188px;top:1410px;width:825px;height:268px;background:var(--green)}
.services-text{left:242px;top:1495px;width:222px;color:#fff;font-size:11.5px;line-height:18.8px}
.services-photo{left:524px;top:1423px;width:477px;height:244px;background:linear-gradient(120deg,#6fd5ea,#3fc4e6 40%,#2a6b7a 70%,#1c3f55)}

/* guarantee */
.checks{left:188px;top:1780px;width:825px;font-size:10.5px;color:#555}
.checks li{list-style:none;display:flex;align-items:center;justify-content:center;gap:6px;height:23px}

/* contact */
.contact{left:188px;top:1868px;width:825px;height:411px;background:var(--blue)}
.contact-head{left:188px;top:1903px;width:825px;text-align:center;font-family:"Ubuntu",sans-serif;font-weight:500;font-size:23px;color:#fff}
.contact-title{left:253px;top:1997px;font-family:"Ubuntu",sans-serif;font-weight:500;font-size:24px;color:#fff}
.contact-text{left:253px;top:2111px;width:260px;color:#fff;font-size:10.2px;line-height:18.7px;font-weight:500}
.label{font-size:10.5px;font-weight:500;color:#fff}
.field{background:#fff}
.submit{left:600px;top:2189px;width:196px;height:45px;border-radius:23px;background:#fff;color:var(--blue);font-size:12px;font-weight:500;display:flex;align-items:center;justify-content:center}

/* ladder area */
.ladder{left:1030px;top:2090px;width:70px;height:480px;border-radius:35px 35px 8px 8px;background:linear-gradient(180deg,rgba(210,220,228,.35),rgba(120,170,220,.25))}

/* footer */
.sea{left:0;top:2320px}
.footer{left:0;top:2440px;width:1200px;height:294px;background:var(--navy)}
.footer-logo{left:188px;top:2492px;font-weight:300;font-size:22px;line-height:24px;color:#fff;letter-spacing:1px}
.footer-about{left:188px;top:2550px;width:190px;font-size:9px;line-height:19px;color:#fff}
.social{left:188px;top:2623px;display:flex;gap:10px}
.social span{width:21px;height:21px;border:1px solid rgba(255,255,255,.5)}
.footer-head{font-family:"Ubuntu",sans-serif;font-weight:500;font-size:19px;color:#fff;top:2512px}
.footer-list{font-size:9px;line-height:19px;color:#fff;list-style:none;top:2550px}
.copyright{left:188px;top:2680px;font-size:9px;color:#fff}
.copyright em{font-style:normal;color:var(--blue-light)}
.legal{left:823px;top:2680px;display:flex;gap:22px;font-size:9px;color:var(--blue-light)}
</style>
</head>
<body>
<div class="page"></div>
<div class="soft-band">
  <svg width="840" height="1020" viewBox="0 0 840 1020"><path d="M380 0 C470 60 560 150 600 260 L840 260 L840 0 Z" fill="#fff" opacity=".6"/></svg>
</div>

<!-- header -->
<div class="abs logo">BRISA<br>LAGOON</div>
<nav class="abs nav"><span class="active">Home</span><span>Our Products</span><span>About Us</span><span>Contact Us</span></nav>
<div class="abs call">
  <div class="call-icon"><svg width="14" height="14" viewBox="0 0 24 24"><path d="M6.6 10.8a15 15 0 006.6 6.6l2.2-2.2a1 1 0 011-.25 11.4 11.4 0 003.6.57 1 1 0 011 1V20a1 1 0 01-1 1A17 17 0 013 4a1 1 0 011-1h3.5a1 1 0 011 1c0 1.25.2 2.45.57 3.57a1 1 0 01-.25 1z" fill="#0094d4"/></svg></div>
  <div><small>Call Now</small><strong>0-(800)-312-55-47</strong></div>
</div>

<!-- hero -->
<div class="abs hero" role="img" aria-label="Wooden-decked above-ground pool in a forest garden"></div>
<h1 class="abs hero-title">Transform Your Garden<br>with Our Premium Above-Ground Pools!</h1>
<p class="abs hero-sub">Achieve your dreams with custom, tailor-made pools.</p>
<div class="abs btn-hero">EXPLORE OUR PRODUCTS</div>

<!-- features -->
<h2 class="abs section-title" style="top:609px">Why Choose Our Above-Ground Pools?</h2>
<div class="abs features">
  <div class="feature highlight"><h3>Superior<br>Quality</h3>
    <svg class="icon" viewBox="0 0 36 36"><circle cx="18" cy="16" r="9" fill="none" stroke="#fff" stroke-width="2"/><path d="M14 16l3 3 5-6" fill="none" stroke="#fff" stroke-width="2"/><path d="M13 24l-2 8 7-3 7 3-2-8" fill="none" stroke="#fff" stroke-width="1.5"/></svg>
    <p>Each pool is constructed with high-quality materials, ensuring exceptional durability and strength.</p></div>
  <div class="feature"><h3>Elegant<br>Design</h3>
    <svg class="icon" viewBox="0 0 36 36"><circle cx="18" cy="18" r="14" fill="var(--foam)"/><circle cx="18" cy="16" r="6" fill="none" stroke="var(--teal)" stroke-width="1.8"/><path d="M15 24h6M16 27h4" stroke="var(--teal)" stroke-width="1.8"/></svg>
    <p>Our pools come in a variety of styles and finishes, seamlessly blending into any garden setting.</p></div>
  <div class="feature"><h3>Custom and<br>Tailor-Made</h3>
    <svg class="icon" viewBox="0 0 36 36"><circle cx="18" cy="18" r="14" fill="var(--foam)"/><circle cx="13" cy="19" r="2.5" fill="var(--teal)"/><circle cx="18" cy="15" r="2.5" fill="var(--teal)"/><circle cx="23" cy="19" r="2.5" fill="var(--teal)"/></svg>
    <p>Create the pool of your dreams with our customization options, tailored to your specific tastes and needs.</p></div>
  <div class="feature"><h3>Easy<br>Installation</h3>
    <svg class="icon" viewBox="0 0 36 36"><circle cx="18" cy="18" r="14" fill="var(--foam)"/><circle cx="18" cy="18" r="9" fill="var(--teal)"/><path d="M14 18l3 3 5-6" fill="none" stroke="#fff" stroke-width="2"/></svg>
    <p>Create the pool of your dreams with our customization options, tailored to your specific tastes and needs.</p></div>
  <div class="feature"><h3>Constant<br>Innovation</h3>
    <svg class="icon" viewBox="0 0 36 36"><circle cx="18" cy="18" r="14" fill="var(--foam)"/><circle cx="18" cy="18" r="9" fill="none" stroke="var(--teal)" stroke-width="1.8" stroke-dasharray="4 3"/></svg>
    <p>Create the pool of your dreams with our customization options, tailored to your specific tastes and needs.</p></div>
</div>

<!-- gallery -->
<h2 class="abs section-title" style="top:918px">Product Showcase</h2>
<div class="photo photo-a" style="left:188px;top:977px;width:323px;height:322px" role="img" aria-label="Boy jumping into a round above-ground pool"></div>
<div class="photo photo-b" style="left:524px;top:977px;width:153px;height:154px" role="img" aria-label="Woman swimming with a beach ball"></div>
<div class="photo photo-c" style="left:689px;top:977px;width:324px;height:154px" role="img" aria-label="Children playing with inflatable rings in a pool"></div>
<div class="photo photo-b" style="left:524px;top:1144px;width:153px;height:155px" role="img" aria-label="Kids splashing in a garden pool"></div>
<div class="photo photo-c" style="left:689px;top:1144px;width:157px;height:155px" role="img" aria-label="Girl with an inflatable toy in a pool"></div>
<div class="photo photo-b" style="left:857px;top:1144px;width:156px;height:155px" role="img" aria-label="Boy swimming in a blue pool"></div>

<!-- services -->
<h2 class="abs section-title" style="top:1358px">Personalized Services</h2>
<div class="abs services"></div>
<svg class="abs" style="left:238px;top:1443px" width="40" height="40" viewBox="0 0 40 40" fill="none" stroke="#fff" stroke-width="2"><circle cx="20" cy="20" r="7"/><circle cx="20" cy="20" r="2.5" fill="#fff"/><path d="M20 4v6M20 30v6M4 20h6M30 20h6M9 9l4 4M27 27l4 4M9 31l4-4M27 13l4-4"/></svg>
<p class="abs services-text">We understand that every garden and client is unique. That’s why we offer personalized services, from design to installation and after-sales support. Our team of experts is here to answer all your questions and guide you throughout your project.</p>
<div class="abs services-photo" role="img" aria-label="Technician checking the liner of a new above-ground pool"></div>

<!-- guarantee -->
<h2 class="abs section-title" style="top:1729px">Guaranteed Satisfaction</h2>
<ul class="abs checks">
  <li><svg width="14" height="12" viewBox="0 0 14 12"><path d="M1 6l4 4 8-9" fill="none" stroke="var(--green)" stroke-width="2.2"/></svg>Emphasize your commitment to quality and customer satisfaction.</li>
  <li><svg width="14" height="12" viewBox="0 0 14 12"><path d="M1 6l4 4 8-9" fill="none" stroke="var(--green)" stroke-width="2.2"/></svg>Mention the 10-year warranty prominently.</li>
</ul>

<!-- contact -->
<div class="abs contact"></div>
<h2 class="abs contact-head">We Bring Your Pool Dreams to Life!</h2>
<h3 class="abs contact-title">Contact Us Today</h3>
<svg class="abs" style="left:252px;top:2053px" width="40" height="36" viewBox="0 0 40 36" fill="none" stroke="#fff" stroke-width="2"><rect x="14" y="2" width="24" height="16" rx="3"/><path d="M2 14h24v14H12l-6 6v-6H2z"/><path d="M8 21h14M19 8h14"/></svg>
<p class="abs contact-text">Don’t wait any longer to transform your garden into a wellness oasis. Contact us today to discover our range of customizable above-ground pools and get a tailored quote.</p>
<div class="abs label" style="left:600px;top:1977px">Your Company Name</div>
<div class="abs field" style="left:600px;top:1999px;width:351px;height:38px"></div>
<div class="abs label" style="left:600px;top:2066px">Your Message</div>
<div class="abs field" style="left:600px;top:2087px;width:351px;height:75px"></div>
<div class="abs submit">SUBMIT</div>

<!-- sea band -->
<svg class="abs sea" width="1200" height="130" viewBox="0 0 1200 130">
  <defs><linearGradient id="seaFade" x1="0" y1="0" x2="0" y2="1"><stop offset="0" stop-color="#0b7fa8"/><stop offset="1" stop-color="#0a3a5c"/></linearGradient></defs>
  <path d="M0 20 C300 0 900 0 1200 20 V130 H0Z" fill="url(#seaFade)"/>
</svg>
<div class="abs ladder" role="img" aria-label="Stainless steel pool ladder"></div>

<!-- footer -->
<footer class="abs footer"></footer>
<div class="abs footer-logo">BRISA<br>LAGOON</div>
<p class="abs footer-about">Feugiat a ligula rutrum luctus primis ultrice nteger congue magna at pretium purus a pretium ligula rutrum and luctus</p>
<div class="abs social"><span></span><span></span><span></span><span></span></div>
<h4 class="abs footer-head" style="left:468px">Resources</h4>
<ul class="abs footer-list" style="left:468px"><li>Our Products,</li><li>About Us</li><li>Contact Us</li></ul>
<h4 class="abs footer-head" style="left:669px">Get In Touch</h4>
<ul class="abs footer-list" style="left:669px"><li>Morel, Lake Road 18</li><li>(+41) 210 - 664 - 905</li><li>Blog Classic</li><li>hello@brisalagoon.ch</li></ul>
<p class="abs copyright">© 2024 - 2025 | Allrights reserved by <em>BRISA LAGOON</em></p>
<div class="abs legal"><span>Terms Privacy</span><span>License</span><span>Privacy Policy</span></div>
</body>
</html>
```